redesign of a candy packaging to enhance the look

Current candy packaging needs to be refreshed and given a more edgy dark look to it. The initial packaging is for a candy company that needs to be a bit less friendly looking, and more dark themed. The idea I have in mind is similar to the current packaging in terms of placements, but I want it to be a dark themed (black/matte grey) with neon blue and pink. similar to being inside a nightclub.

Target Market(s)

19-40

Requirements
Must have
• text and images from original packaging
dark themed to make more adult friendly
usage of neon colours
Nice to have
• on the back have some fruits scattered around

**The main focus shall be on the TIPSY FOX. and the Zelmo bar should be off to the side

**the teddy bear shall be sitting on the letters of Tipsy fox

**Use one big "B" when using Tipsy foxes instead of two "B's"
Should not have
• kid theme

```html
<!DOCTYPE html>
<html lang="en">
<head>
<meta charset="utf-8">
<title>Tipsy Foxz – Alcoholic Candy Pouch</title>
<link rel="stylesheet" href="https://fonts.googleapis.com/css2?family=Fredoka:wght@500;600;700&family=Gochi+Hand&display=swap">
<style>
  :root {
    --backdrop: #e2e2e4;
    --pouch-navy: #1c2140;
    --pouch-deep: #14172e;
    --glow-blue: #3d4fe8;
    --glow-violet: #6a3be0;
    --glow-pink: #e05ac8;
    --glow-amber: #f3c46a;
    --ink-white: #f2f2f4;
    --title-cyan: #47b6e8;
    --title-edge: #0f2a44;
    --brand-teal: #5fcbb0;
    --brand-orange: #f08a2a;
    --label-blue: #5060f0;
  }
  * { box-sizing: border-box; margin: 0; padding: 0; }
  html, body {
    width: 1077px; height: 1200px; overflow: hidden;
    background: var(--backdrop);
  }
  .pouch {
    position: absolute; left: 171px; top: 0;
    width: 735px; height: 1200px;
    background:
      radial-gradient(ellipse 150px 170px at 400px 420px, rgba(243,196,106,.85), rgba(243,196,106,0) 70%),
      radial-gradient(ellipse 260px 230px at 230px 560px, rgba(61,79,232,.9), rgba(61,79,232,0) 75%),
      radial-gradient(ellipse 300px 200px at 380px 700px, rgba(106,59,224,.75), rgba(106,59,224,0) 75%),
      radial-gradient(ellipse 300px 190px at 300px 930px, rgba(224,90,200,.85), rgba(224,90,200,0) 75%),
      linear-gradient(180deg, var(--pouch-navy), var(--pouch-deep));
    font-family: "Fredoka", sans-serif;
    color: var(--ink-white);
  }
  .zip-band {
    position: absolute; left: 0; right: 0; top: 200px;
    height: 2px; background: rgba(255,255,255,.08);
  }
  .tear-label {
    position: absolute; left: 119px; top: 88px;
    font-family: "Gochi Hand", sans-serif; font-size: 13px; letter-spacing: .5px;
  }
  .tear-line {
    position: absolute; left: 78px; top: 110px; width: 578px; height: 4px;
    border-top: 2px dashed var(--ink-white);
  }
  .tear-arrow { position: absolute; left: 76px; top: 104px; }
  .reseal {
    position: absolute; top: 124px;
    font-family: "Gochi Hand", sans-serif; font-size: 24px; letter-spacing: 1px;
  }
  .reseal--fr { left: 90px; }
  .reseal--en { right: 91px; }
  .maker-name {
    position: absolute; left: 150px; top: 372px;
    font-size: 24px; font-weight: 700; color: var(--brand-teal); letter-spacing: 1px;
  }
  .range-name {
    position: absolute; left: 456px; top: 328px; width: 180px;
    font-size: 44px; font-weight: 700; line-height: .95; color: var(--brand-orange);
    text-align: center;
  }
  .mascot {
    position: absolute; left: 285px; top: 432px; width: 200px; height: 300px;
    border-radius: 90px 90px 60px 60px;
    background: radial-gradient(ellipse at 50% 40%, #5f86f0, #3457d8 70%);
  }
  .product-title {
    position: absolute; left: 187px; top: 740px; width: 400px;
    text-align: center; font-weight: 700; color: var(--title-cyan);
    font-size: 92px; line-height: .98; letter-spacing: 1px;
  }
  .product-type {
    position: absolute; left: 187px; top: 952px; width: 400px;
    text-align: center; font-weight: 600; color: var(--title-cyan);
    font-size: 46px; line-height: 1.1;
  }
  .net-weight {
    position: absolute; left: 119px; top: 1090px;
    font-size: 32px; font-weight: 600; color: var(--label-blue);
  }
  .flavour-note {
    position: absolute; right: 117px; top: 1093px; text-align: right;
    font-family: "Gochi Hand", sans-serif; font-size: 15px; line-height: 1.1;
    color: var(--label-blue);
  }
</style>
</head>
<body>
  <div class="pouch">
    <div class="tear-label">TEAR HERE / DÉCHIRER</div>
    <svg class="tear-arrow" width="14" height="18" viewBox="0 0 14 18"><path d="M0 0 L14 9 L0 18 Z" fill="#f2f2f4"/></svg>
    <div class="tear-line"></div>
    <div class="reseal reseal--fr">REFERMABLE</div>
    <div class="reseal reseal--en">RESEALABLE</div>
    <div class="zip-band"></div>

    <div class="maker-name">MARLOW'S</div>
    <div class="range-name">ZELMO BAR</div>

    <div class="mascot" role="img" aria-label="Blue cartoon mascot in a cap, sitting on the product title"></div>

    <h1 class="product-title">TIPSY<br>FOXZ</h1>
    <p class="product-type">ALCOHOLIC<br>CANDY</p>

    <div class="net-weight">00 oz</div>
    <div class="flavour-note">ARTIFICIAL FLAVORS<br>ARÔME ARTIFICIEL</div>
  </div>
</body>
</html>
```